Black Friday Specials for Car Styling Services and Products

I’m not sure of the exact design on this. Will leave to your creative talents. I’ve attached some of the other things we have done to help but need the black Friday vibe. More emphasis on the BF prices vs. the normal prices. Maybe use a starburst for special financing. Thanks.

Target Market(s)

Holiday Shoppers

Requirements
Must have
• Black Friday feel/look
Nice to have
• I like watermarked pictures as the back drop. See the other flyers I attached.

```html
<!DOCTYPE html>
<html lang="en">
<head>
<meta charset="utf-8">
<title>Black Friday Specials – Gloss Haven</title>
<link href="https://fonts.googleapis.com/css2?family=Montserrat:ital,wght@0,500;0,600;0,700;0,800;0,900;1,800;1,900&family=Poppins:wght@500;600;700;800&family=Kaushan+Script&family=Roboto:wght@500&display=swap" rel="stylesheet">
<style>
  :root{
    --bg-dark:#151515;
    --bg-mid:#3b3b3b;
    --gold:#f4d21f;
    --gold-deep:#b88a00;
    --yellow-cell:#e9c300;
    --orange-cell:#ef9b19;
    --grey-light:#ececec;
    --grey-mid:#b6b4b0;
    --green-bright:#0fbe12;
    --green-deep:#0a8c0d;
    --red:#e01010;
    --red-deep:#9a0000;
    --white:#ffffff;
    --ink:#151515;
  }
  *{box-sizing:border-box;margin:0;padding:0}
  html,body{width:868px;height:1200px;overflow:hidden;background:#c4c4c4}
  .flyer{position:relative;width:868px;height:1200px;overflow:hidden;
    background:radial-gradient(ellipse at 55% 35%,var(--bg-mid) 0%,#242424 55%,var(--bg-dark) 100%);
    font-family:'Montserrat',sans-serif;color:var(--white)}
  .paper{position:absolute;inset:0;width:868px;height:1200px}

  .headline{position:absolute;left:0;top:0;width:540px;height:360px}
  .headline svg{width:540px;height:360px;display:block}
  .headline-word{font-family:'Montserrat',sans-serif;font-weight:900}
  .specials-word{font-family:'Kaushan Script',cursive;stroke:#fff;stroke-width:3;paint-order:stroke fill}
  .tagline{position:absolute;left:319px;top:264px;font-size:12.5px;font-weight:500;line-height:15.7px;white-space:nowrap}

  .divider{position:absolute;left:532px;top:50px;width:1px;height:361px;background:rgba(255,255,255,.35)}
  .tier{position:absolute;left:591px}
  .tier-label{font-size:14px;font-weight:700;letter-spacing:2.8px;line-height:16px;white-space:nowrap}
  .tier-amount{font-family:'Poppins',sans-serif;font-weight:800;font-size:30px;line-height:36px;margin-top:1px;white-space:nowrap}
  .tier-amount sup{font-size:15px;vertical-align:top;position:relative;top:-3px}
  .tier-button{margin-top:6px;width:127px;height:31px;border-radius:5px;
    background:linear-gradient(180deg,#ffe437,var(--gold) 60%,#c9a000);color:var(--ink);
    font-family:'Poppins',sans-serif;font-weight:800;font-size:15.5px;line-height:32px;text-align:center;
    box-shadow:0 2px 3px rgba(0,0,0,.6)}
  .tier-rule{position:absolute;left:589px;width:208px;border-top:1px dashed var(--gold)}

  .car-photo{position:absolute;left:43px;top:361px;width:518px;height:240px;border-radius:45% 30% 20% 30% / 50% 40% 30% 35%;
    background:radial-gradient(ellipse at 60% 45%,#ffe84a 0%,#f0c400 50%,#6b5600 90%)}
  .starburst{position:absolute;left:539px;top:424px;width:152px;height:152px}
  .starburst-text{position:absolute;left:549px;top:450px;font-family:'Poppins',sans-serif;line-height:1;white-space:nowrap}
  .starburst-text .up{font-size:20px;font-weight:700;letter-spacing:3px;line-height:26px}
  .starburst-text .pct{font-size:40px;font-weight:800;line-height:30px}
  .starburst-text .off{font-size:42px;font-weight:500;line-height:36px}
  .finance{position:absolute;left:692px;top:423px;font-family:'Poppins',sans-serif;font-size:17.5px;font-weight:600;line-height:20.6px;white-space:nowrap}

  .savings-title{position:absolute;left:0;top:590px;width:868px;height:30px}
  .savings-title svg{display:block;width:868px;height:30px}
  .savings-text{font-family:'Montserrat',sans-serif;font-weight:900;font-style:italic}

  .col-tab{position:absolute;height:31px;border-radius:12px 12px 0 0;background:linear-gradient(180deg,#c41414,var(--red-deep));
    font-size:12px;font-weight:800;font-style:italic;text-align:center;line-height:34px;white-space:nowrap}
  .tab-product{left:55px;top:667px;width:174px}
  .tab-featured{left:250px;top:667px;width:175px}
  .tab-bf{left:471px;top:651px;width:141px;z-index:3;line-height:30px}
  .tab-retail{left:661px;top:667px;width:143px}

  .price-table{position:absolute;left:41px;top:698px;width:786px}
  .price-row{position:relative;height:26.2px}
  .cell{position:absolute;top:1px;height:24.2px;display:flex;align-items:center;justify-content:center;
    font-family:'Roboto',sans-serif;font-size:10.5px;color:var(--ink);text-align:center;line-height:1.05}
  .cell-product{left:0;width:197px;border-radius:9px 0 0 9px;background:var(--yellow-cell)}
  .cell-featured{left:199px;width:192px;background:var(--grey-light)}
  .cell-retail{left:590px;width:196px;padding-left:20px;background:var(--grey-light);font-size:14px}
  .price-row:nth-child(even) .cell-product{background:var(--orange-cell)}
  .price-row:nth-child(even) .cell-featured,.price-row:nth-child(even) .cell-retail{background:var(--grey-mid)}
  .price-row:first-child .cell-retail{border-top-right-radius:16px}
  .price-row:last-child .cell-retail{border-bottom-right-radius:16px}
  .bf-price{position:absolute;left:393px;width:204px;top:1px;height:24.2px;z-index:3;text-align:center;
    font-family:'Roboto',sans-serif;font-size:14px;line-height:24px;color:var(--white)}
  .bolt{position:absolute;left:0;top:0;width:868px;height:1200px;z-index:2}

  .brand{position:absolute;left:38px;top:1070px;display:flex;align-items:center;gap:8px;
    font-family:'Montserrat',sans-serif;font-weight:900;font-size:33px;line-height:40px;color:var(--ink);letter-spacing:1px;white-space:nowrap}
  .brand-dot{width:16px;height:16px;border-radius:50%;background:var(--yellow-cell)}
  .brand-sub{position:absolute;left:62px;top:1112px;font-size:10.5px;font-weight:600;letter-spacing:2.2px;color:var(--ink);white-space:nowrap}
  .visit{position:absolute;left:409px;top:1091px;width:120px;height:26px;background:var(--yellow-cell);
    color:var(--ink);font-weight:900;font-style:italic;font-size:17px;letter-spacing:3px;text-align:center;line-height:27px}
  .url{position:absolute;left:531px;top:1090px;width:296px;height:27px;border:1px solid #777;border-radius:0 5px 5px 0;
    color:var(--ink);font-weight:800;font-style:italic;font-size:17px;letter-spacing:3.4px;text-align:center;line-height:26px}
  .fine-print{position:absolute;left:52px;top:1143px;width:764px;font-size:8.6px;line-height:11px;color:var(--ink);text-align:center}
  .fine-print b{font-weight:700}
</style>
</head>
<body>
<main class="flyer">

  <h1 class="headline" aria-label="Black Friday Specials">
    <svg viewBox="0 0 540 360" aria-hidden="true">
      <defs>
        <linearGradient id="goldFill" x1="0" y1="53" x2="0" y2="147" gradientUnits="userSpaceOnUse">
          <stop offset="0" stop-color="#f8e36a"/><stop offset=".5" stop-color="#f4d21f"/><stop offset="1" stop-color="#b88a00"/>
        </linearGradient>
        <linearGradient id="silverFill" x1="0" y1="162" x2="0" y2="251" gradientUnits="userSpaceOnUse">
          <stop offset="0" stop-color="#ffffff"/><stop offset=".5" stop-color="#d8d8d8"/><stop offset="1" stop-color="#7b7b7b"/>
        </linearGradient>
      </defs>
      <text class="headline-word" x="46" y="147" font-size="134" textLength="424" lengthAdjust="spacingAndGlyphs" fill="url(#goldFill)">BLACK</text>
      <text class="headline-word" x="48" y="251" font-size="127" textLength="418" lengthAdjust="spacingAndGlyphs" fill="url(#silverFill)">FRIDAY</text>
      <text class="specials-word" x="44" y="330" font-size="78" textLength="240" lengthAdjust="spacingAndGlyphs" fill="#e01010" transform="rotate(-5 160 310)">Specials</text>
      <text class="specials-word" x="289" y="296" font-size="48" fill="#e01010">*</text>
    </svg>
  </h1>
  <p class="tagline">Incredible deals on<br>window tint, paint<br>protection film, color<br>change wraps and<br>ceramic coating!</p>

  <div class="divider"></div>

  <div class="tier" style="top:50px">
    <div class="tier-label">PURCHASES UP TO</div>
    <div class="tier-amount"><sup>$</sup>249.99</div>
    <div class="tier-button">GET 10% OFF</div>
  </div>
  <div class="tier-rule" style="top:161px"></div>
  <div class="tier" style="top:176px">
    <div class="tier-label">PURCHASES BETWEEN</div>
    <div class="tier-amount"><sup>$</sup>250 &amp; <sup>$</sup>650</div>
    <div class="tier-button">GET 15% OFF</div>
  </div>
  <div class="tier-rule" style="top:284px"></div>
  <div class="tier" style="top:302px">
    <div class="tier-label">PURCHASES OF</div>
    <div class="tier-amount"><sup>$</sup>650+</div>
    <div class="tier-button">GET 20% OFF</div>
  </div>

  <div class="car-photo" role="img" aria-label="Photo of a glossy yellow sports coupe, front three-quarter view"></div>

  <svg class="starburst" viewBox="0 0 170 170" aria-hidden="true">
    <defs>
      <radialGradient id="burstFill" cx="50%" cy="45%" r="55%">
        <stop offset="0" stop-color="#e81818"/><stop offset="1" stop-color="#8c0000"/>
      </radialGradient>
    </defs>
    <polygon fill="url(#burstFill)" points="85,2 93,14 104,4 108,18 121,11 121,25 135,22 131,36 146,36 139,49 153,53 143,63 156,71 144,78 155,88 142,93 150,105 137,107 142,120 128,119 130,133 117,129 115,143 103,136 98,150 88,140 80,152 74,139 63,149 60,135 47,141 47,127 33,129 37,116 23,114 30,102 17,96 28,88 17,78 30,73 22,62 36,59 31,46 45,46 44,33 58,36 60,22 72,28 77,14"/>
  </svg>
  <div class="starburst-text">
    <div class="up">UP TO</div>
    <div class="pct">20%</div>
    <div class="off">OFF</div>
  </div>
  <p class="finance">Plus, special<br>90 day,<br>no interest<br>payment plan<br>for purchases<br>over $650**</p>

  <svg class="paper" viewBox="0 0 868 1200" aria-hidden="true">
    <polygon fill="#ffffff" points="0,996 20,1001 38,995 60,1003 90,998 120,1006 160,1002 200,1012 240,1010 280,1022 320,1034 360,1044 400,1050 440,1056 480,1060 520,1060 560,1062 600,1056 640,1044 680,1028 720,1010 760,996 800,988 840,982 868,980 868,1200 0,1200"/>
  </svg>

  <h2 class="savings-title" aria-label="Other great Black Friday savings (installation included!!)">
    <svg viewBox="0 0 868 30" aria-hidden="true">
      <text class="savings-text" x="80" y="23" font-size="20" textLength="712" lengthAdjust="spacingAndGlyphs" fill="#ffffff">OTHER GREAT BLACK FRIDAY SAVINGS <tspan fill="#f4d21f">(INSTALLATION INCLUDED!!)</tspan></text>
    </svg>
  </h2>

  <div class="col-tab tab-product">Product/Service</div>
  <div class="col-tab tab-featured">Featured Item</div>
  <div class="col-tab tab-bf">Black Friday Price</div>
  <div class="col-tab tab-retail">Retail Price</div>

  <svg class="bolt" viewBox="0 0 868 1200" aria-hidden="true">
    <defs>
      <clipPath id="boltShape">
        <polygon points="434,683 655,683 606,845 661,824 618,1045 434,1045"/>
      </clipPath>
    </defs>
    <polygon points="434,681 658,681 611,841 665,820 620,1047 434,1047" fill="#111"/>
    <g clip-path="url(#boltShape)">
      <rect x="434" y="683" width="240" height="362" fill="var(--green-bright)"/>
      <rect x="434" y="724.2" width="240" height="26.2" fill="var(--green-deep)"/>
      <rect x="434" y="776.6" width="240" height="26.2" fill="var(--green-deep)"/>
      <rect x="434" y="829" width="240" height="26.2" fill="var(--green-deep)"/>
      <rect x="434" y="881.4" width="240" height="26.2" fill="var(--green-deep)"/>
      <rect x="434" y="933.8" width="240" height="26.2" fill="var(--green-deep)"/>
      <rect x="434" y="986.2" width="240" height="26.2" fill="var(--green-deep)"/>
    </g>
  </svg>

  <section class="price-table">
    <div class="price-row"><div class="cell cell-product">Remote Start</div><div class="cell cell-featured">Premium package</div><div class="bf-price">$299</div><div class="cell cell-retail">$349</div></div>
    <div class="price-row"><div class="cell cell-product">Remote Start</div><div class="cell cell-featured">Supreme package</div><div class="bf-price">$399</div><div class="cell cell-retail">$479</div></div>
    <div class="price-row"><div class="cell cell-product">Remote Start</div><div class="cell cell-featured">Ultimate package</div><div class="bf-price">$599</div><div class="cell cell-retail">$679</div></div>
    <div class="price-row"><div class="cell cell-product">Subwoofer Truck</div><div class="cell cell-featured">Premium package</div><div class="bf-price">$749</div><div class="cell cell-retail">$849</div></div>
    <div class="price-row"><div class="cell cell-product">Subwoofer Truck</div><div class="cell cell-featured">Supreme package</div><div class="bf-price">$999</div><div class="cell cell-retail">$1,149</div></div>
    <div class="price-row"><div class="cell cell-product">Subwoofer Truck</div><div class="cell cell-featured">Ultimate package</div><div class="bf-price">$1,299</div><div class="cell cell-retail">$1,489</div></div>
    <div class="price-row"><div class="cell cell-product">Dash Cam</div><div class="cell cell-featured">2K QHD, LTE + GPS +WiFi</div><div class="bf-price">$459</div><div class="cell cell-retail">$579</div></div>
    <div class="price-row"><div class="cell cell-product">Dash Cam</div><div class="cell cell-featured">1080p Full HD, Wifi,</div><div class="bf-price">$299</div><div class="cell cell-retail">$399</div></div>
    <div class="price-row"><div class="cell cell-product">Amplifier Upgrade</div><div class="cell cell-featured">1,500-Watt Subwoofer amp</div><div class="bf-price">$549</div><div class="cell cell-retail">$699</div></div>
    <div class="price-row"><div class="cell cell-product">Amplifier Upgrade</div><div class="cell cell-featured">500-Watt 4-speaker amp</div><div class="bf-price">$379</div><div class="cell cell-retail">$499</div></div>
    <div class="price-row"><div class="cell cell-product">Underbody Glow</div><div class="cell cell-featured">Chasing Lighting</div><div class="bf-price">$349</div><div class="cell cell-retail">$435</div></div>
    <div class="price-row"><div class="cell cell-product">Wheel Well Lights</div><div class="cell cell-featured">8-Piece Rock Lights</div><div class="bf-price">$299</div><div class="cell cell-retail">$399</div></div>
    <div class="price-row"><div class="cell cell-product">Marine Upgrade</div><div class="cell cell-featured">Dual 10”, 300-Watt tower speakers/<br>tweeter array</div><div class="bf-price">$1,699</div><div class="cell cell-retail">$1,899</div></div>
  </section>

  <div class="brand"><span class="brand-dot"></span>GLOSS HAVEN</div>
  <div class="brand-sub">CAR CARE &amp; STYLING STUDIOS</div>
  <div class="visit">VISIT US</div>
  <div class="url">www.glosshaven.com</div>

  <p class="fine-print"><b>*Pricing available until December 1</b> **Special 90-day payment plan: Only ½ due at the time of purchase. The balance is due in three equal payments over 30, 60 and 90 days. For example, for a $500 purchase only $250 is due at the time of the sale. Then three equal payments of $83.33 at 30, 60 and 90 days. Limited availability.</p>

</main>
</body>
</html>
```